LIFE CHANGING NEW WEBSITE DESIGN NEEDED FOR FULL WEBSITE- FUN/FEMININE!

I need a website designed for a personal financial advice website geared at women called BLUE OTTER LANTERN. I will be providing free financial advice around topics of making, saving, spending and sharing money. The concept is to change the way women understand money and the necessity around building various passive income streams to ensure full financial freedom. This will then carry down to advice for mothers with children and children in particular. The website should be elegant and yet witty. I don't want lots of serious photos but more relatable. I will have a photo of myself and my story as this is a blog and needs to be relatable to women and mothers. I like pinks and greys. I want to have a pink piggy bank being broken with a hammer in the front screen to break our traditional mindset around piggy bank saving/spending habits. I have created a logo that is a pink piggy head with BLUE OTTER LANTERN that needs to be incorporated so that it blends into the heading. I have also already started designing the website on Squarespace and can provide access to that. Basically it should have a format of BLUE OTTER LANTERN LOGO center in header then on left hand navigation: MAKE, SAVE, SPEND, SHARE then on right hand header navigation: MISSION, GET STARTED, CONTACT BOL I would like to have the front page when you go to the url to have the image of the piggy bank being broken then a catchy phrase then under 4 boxes with MAKE (image and description) SAVE (image and description) SPEND (image and description) SHARE (image and description) if you click on those or the title they go to pages that are dedicated to each them. Each page should have a little intro on the topic then I want lots of blog links as I will be mainly writing blogs. Each blog site should have ability to write comments as well. I need social media icons on each page too. Please let me know what you need from me to get started. I prefer having a discussion if possible to not waste anyone's time. I need the site to be easy for me to use and add blogs/urls etc as needed. I also need the site to be put into my domain that I already purchased: www.blueotterlantern-sample.com

Target Market(s)

teenage girls, 20 something girls, 30 something girls and mothers

Coding

Coded - Design and coding required

Number of Pages Required

5+ page

Font styles to use
Sans Serif

Colors
e667a6
e34197
f59195
eea4c8
aaaaaa
cbcbcb
959595

Requirements
Must have
• TOP NAVIGATION
• MAKE SAVE SPEND SHARE LOGO/BLUE OTTER LANTERN MISSION GET STARTED CONTACT BOL
• FRONT PAGE: IMAGE OF PIGGY BANK BEING BROKEN WITH A HAMMER
• CATCH PHRASE OVER THE IMAGE
• BUTTON IN PINK- TAKE ACTION (WHICH DIRECTS TO TAKE ACTION TAB ON NAVIGATION HEADER
• 4 BOXES BELOW MAIN IMAGE WITH IMAGE/DESCRIPTIONS FOR MAKE, SAVE, SPEND, SHARE THAT EACH GO TO THE PAGES FROM THE NAVIGATION HEADER
• EACH PAGE SHOULD BE DEDICATED TO THOSE TOPICS THEN THERE IS AN INTRO ON EACH PAGE THEN THE LINKS TO DIFFERENT BLOGS AROUND EACH TOPIC FOR MAKE, SAVE, SPEND, SHARE
• EACH BLOG SHOULD HAVE COMMENTS SECTION AND SOCIAL MEDIA ICONS
• (GOOD TO USE PINKS/GREYS)
Should not have
• BE SUPER BUSY, CLUTTERED, FEEL LIKE I AM SELLING SOMETHING

```html
<!DOCTYPE html>
<html lang="en">
<head>
<meta charset="utf-8">
<title>Blue Otter Lantern</title>
<link href="https://fonts.googleapis.com/css2?family=Zilla+Slab:ital,wght@0,300;0,400;0,600;1,400&display=swap" rel="stylesheet">
<style>
  :root {
    --pink: #e667a6;
    --pink-deep: #e34197;
    --ink: #222222;
    --text: #555555;
    --nav: #959595;
    --line: #ececec;
    --tan: #d4b59c;
    --white: #ffffff;
  }
  * { margin: 0; padding: 0; box-sizing: border-box; }
  html, body { width: 1200px; height: 595px; overflow: hidden; background: var(--white); }
  body { position: relative; font-family: "Zilla Slab", Georgia, serif; color: var(--ink); }

  .top-rule { position: absolute; left: 0; top: 0; width: 1200px; height: 2px; background: var(--pink); }

  .site-header {
    position: absolute; left: 0; top: 2px; width: 1200px; height: 47px;
    border-bottom: 1px solid var(--line);
    box-shadow: 0 1px 3px rgba(0,0,0,0.03);
  }
  .main-nav a {
    position: absolute; top: 17px; font-size: 10px; color: var(--nav);
    text-decoration: none; transform: translateX(-50%); white-space: nowrap;
  }

  .topic-card { position: absolute; top: 76px; width: 156px; text-align: center; }
  .topic-frame {
    width: 156px; height: 156px; padding: 3px; background: var(--white);
    box-shadow: 0 0 2px rgba(0,0,0,0.12);
  }
  .topic-photo { width: 100%; height: 100%; }
  .topic-dash { width: 10px; height: 1px; background: var(--pink); margin: 5px auto 0; }
  .topic-title { font-size: 15px; font-weight: 600; margin-top: 10px; color: var(--ink); }

  .guide-cover {
    position: absolute; left: 278px; top: 329px; width: 218px; height: 280px;
    border-left: 2px solid #cfe9e8;
    box-shadow: 0 0 2px rgba(0,0,0,0.15);
  }

  .guide-copy { position: absolute; left: 539px; top: 338px; width: 380px; }
  .guide-title { font-size: 16.5px; font-weight: 400; line-height: 18px; color: var(--ink); }
  .guide-title em { font-style: italic; }
  .guide-lead { margin-top: 15px; font-size: 8px; line-height: 12.5px; font-weight: 300; color: var(--text); }
  .guide-points { list-style: none; margin-top: 13px; }
  .guide-points li {
    position: relative; padding-left: 12px; font-size: 8px; line-height: 18.5px; color: var(--ink);
  }
  .guide-points li::before {
    content: ""; position: absolute; left: 0; top: 8px; width: 3px; height: 3px;
    border-radius: 50%; background: var(--pink);
  }
  .download-btn {
    position: absolute; left: 539px; top: 510px; width: 80px; height: 29px;
    background: var(--tan); color: var(--white); font-size: 8px;
    display: flex; align-items: center; justify-content: center; text-decoration: none;
  }
  .back-to-top { position: absolute; left: 1169px; top: 529px; width: 12px; height: 12px; }
</style>
</head>
<body>
  <div class="top-rule"></div>

  <header class="site-header">
    <nav class="main-nav">
      <a href="#" style="left:429px">Make</a>
      <a href="#" style="left:475px">Save</a>
      <a href="#" style="left:523px">Spend</a>
      <a href="#" style="left:574px">Share</a>
      <a href="#" style="left:629px">Mission</a>
      <a href="#" style="left:696px">Get Started</a>
      <a href="#" style="left:772px">Contact Me</a>
    </nav>
  </header>

  <section class="topics">
    <a class="topic-card" href="#" style="left:267px; text-decoration:none">
      <div class="topic-frame">
        <div class="topic-photo" role="img" aria-label="Photo of a woman working on a laptop at a bright desk" style="background:linear-gradient(135deg,#e4ddd6,#c9b6ac 55%,#eeeae6)"></div>
      </div>
      <div class="topic-dash"></div>
      <div class="topic-title">Make</div>
    </a>
    <a class="topic-card" href="#" style="left:437px; text-decoration:none">
      <div class="topic-frame">
        <div class="topic-photo" role="img" aria-label="Photo of a pink piggy bank behind stacks of coins" style="background:linear-gradient(160deg,#ffffff 30%,#f4a6cf 60%,#d9a468 100%)"></div>
      </div>
      <div class="topic-dash"></div>
      <div class="topic-title">Save</div>
    </a>
    <a class="topic-card" href="#" style="left:607px; text-decoration:none">
      <div class="topic-frame">
        <div class="topic-photo" role="img" aria-label="Photo of banknotes, coins and a red wallet on marble" style="background:linear-gradient(200deg,#d7cfc0 0%,#ebebea 35%,#e4e4e3 100%)"></div>
      </div>
      <div class="topic-dash"></div>
      <div class="topic-title">Spend</div>
    </a>
    <a class="topic-card" href="#" style="left:777px; text-decoration:none">
      <div class="topic-frame">
        <div class="topic-photo" role="img" aria-label="Photo of three friends in sun hats laughing on a bench" style="background:linear-gradient(180deg,#f1efe9 0%,#e9dccd 55%,#d9c7b3 100%)"></div>
      </div>
      <div class="topic-dash"></div>
      <div class="topic-title">Share</div>
    </a>
  </section>

  <section class="guide">
    <div class="guide-cover" role="img" aria-label="Cover illustration of the free financial freedom guide with a piggy bank and coins" style="background:linear-gradient(160deg,#f9d5dc 0%,#f7c9d3 55%,#f3e0e6 100%)"></div>

    <div class="guide-copy">
      <h2 class="guide-title"><em>Get your Life Changing and Fulfillment</em> Free Guide Today</h2>
      <p class="guide-lead">Blue Otter Lantern will empower you to eliminate obstacles, gain clarity, set goals and holds you accountable to achieve your financial freedom</p>
      <ul class="guide-points">
        <li>Discover the roots of your problems</li>
        <li>Achieve happiness within months</li>
        <li>Get discount on programs</li>
        <li>Discover the roots of your problems</li>
      </ul>
    </div>
    <a class="download-btn" href="#">Download</a>
  </section>

  <svg class="back-to-top" viewBox="0 0 12 12" aria-label="Back to top">
    <path d="M6 1 L11 6 H8 V11 H4 V6 H1 Z" fill="#9a9a9a"/>
  </svg>
</body>
</html>
```